Design a product reviews website

We need a website design and simple logo for the brand Venlotix.com. The website will provide reviews of technology products and services. The brand and website should be approachable but should also be trustworthy and high quality. The deliverable should be designs, specs and assets that I can provide to a development team to build the website.

Target Market(s)

People researching products to buy.

Industry/Entity Type

Product

Logo Text

Venlotix.com

Number of Pages Required

5+ page

Font styles to use
Sans Serif

Colors
0492cd
0355a3
3176b5
33a6d7
85cae6
85abd2
cedeed
cee9f5

Requirements
Must have
• - Designs for the Homepage, Category and Article pages.
• - Designs for web and mobile.
• - Designs details for the engineering team to use for development.
• - I'm open to other colors than the preferences I chose but I'm more likely to like blues, greys and blacks.

```html
<!DOCTYPE html>
<html lang="en">
<head>
<meta charset="utf-8">
<title>Venlotix.com – Product Reviews</title>
<link href="https://fonts.googleapis.com/css2?family=Open+Sans:wght@400;600;700&display=swap" rel="stylesheet">
<style>
  :root{
    --blue:#3176b5;
    --blue-bright:#0492cd;
    --page:#e9e9e9;
    --panel:#ffffff;
    --line:#dcdcdc;
    --text:#333333;
    --muted:#888888;
    --footer:#1e1e1e;
    --loadmore:#8c8c8c;
  }
  *{box-sizing:border-box;margin:0;padding:0}
  html,body{width:833px;height:1200px;overflow:hidden}
  body{position:relative;background:var(--page);font-family:"Open Sans",Arial,sans-serif;color:var(--text)}
  .abs{position:absolute}

  .site-header{left:0;top:0;width:833px;height:36px;background:var(--panel)}
  .brand{left:16px;top:8px;font-weight:600;font-size:16px;line-height:20px;color:var(--text)}
  .search{left:498px;top:10px;width:210px;height:20px;border:1px solid var(--line);display:flex}
  .search-input{flex:1;font-size:9px;color:var(--muted);padding:4px 6px}
  .search-btn{width:26px;background:var(--blue);display:flex;align-items:center;justify-content:center}
  .menu-btn{left:735px;top:10px;width:26px;height:20px;border:1px solid var(--line);display:flex;align-items:center;justify-content:center}

  .hero{left:0;top:36px;width:833px;height:284px;background:linear-gradient(90deg,#6b655e 0%,#a69c90 40%,#d9d2c8 70%,#8a8279 100%)}
  .hero-title{left:54px;top:152px;width:400px;font-size:22px;line-height:29px;color:#fff;font-weight:400;text-shadow:0 1px 3px rgba(0,0,0,.4)}
  .hero-dots{left:54px;top:252px;display:flex;gap:5px}
  .hero-dots span{width:7px;height:7px;border-radius:50%;background:rgba(255,255,255,.6)}
  .hero-dots span:first-child{background:#fff}

  .category-nav{left:47px;top:333px;width:139px;background:var(--panel)}
  .category-nav li{list-style:none;height:37px;display:flex;align-items:center;gap:9px;padding-left:10px;font-size:9px;color:#555;border-bottom:1px solid var(--line);text-transform:uppercase}
  .category-nav li.active{background:var(--blue);color:#fff}
  .category-nav svg{flex:none}

  .column{background:var(--panel)}
  .column-title{font-size:10px;font-weight:600;color:#555;text-transform:uppercase;padding:14px 12px 0}
  .new-products{left:208px;top:333px;width:384px;height:764px}
  .popular{left:611px;top:333px;width:175px;height:805px}

  .photo{position:relative}
  .tags{position:absolute;right:6px;bottom:6px;display:flex;gap:3px}
  .tag{background:var(--blue);color:#fff;font-size:8px;padding:3px 7px;text-transform:uppercase}
  .card-title{font-weight:600;color:#444}
  .card-title.large{font-size:14px;line-height:18px;margin-top:12px}
  .card-title.small{font-size:12px;line-height:16px;margin-top:10px}
  .card-title.side{font-size:11px;line-height:15px;margin-top:6px}
  .byline{display:flex;align-items:center;gap:8px;font-size:8px;color:var(--muted);margin-top:9px}
  .avatar{width:22px;height:22px;background:#9aa3ad}
  .author{color:var(--blue);font-size:9px;flex:1}

  .load-more{left:208px;top:1111px;width:578px;height:33px;background:var(--loadmore);display:flex;align-items:center;justify-content:center;gap:6px;color:#fff;font-size:10px}

  .site-footer{left:0;top:1161px;width:833px;height:39px;background:var(--footer);color:#bbb;font-size:9px;display:flex;align-items:center;justify-content:center}
</style>
</head>
<body>

<header class="site-header abs">
  <div class="brand abs">Venlotix.com</div>
  <div class="search abs">
    <span class="search-input">Search for products</span>
    <span class="search-btn"><svg width="10" height="10" viewBox="0 0 10 10"><circle cx="4" cy="4" r="3" fill="none" stroke="#fff" stroke-width="1.4"/><line x1="6.3" y1="6.3" x2="9.3" y2="9.3" stroke="#fff" stroke-width="1.4"/></svg></span>
  </div>
  <div class="menu-btn abs"><svg width="12" height="10" viewBox="0 0 12 10"><rect y="0" width="12" height="2" fill="#666"/><rect y="4" width="12" height="2" fill="#666"/><rect y="8" width="12" height="2" fill="#666"/></svg></div>
</header>

<section class="hero abs" role="img" aria-label="Photo of a modern kitchen with a smiling man in a suit giving two thumbs up"></section>
<h1 class="hero-title abs">The Best Product and Services<br>Reviews and Rankings</h1>
<div class="hero-dots abs"><span></span><span></span><span></span></div>

<nav>
<ul class="category-nav abs">
  <li class="active"><svg width="12" height="11" viewBox="0 0 12 11"><path d="M1 6 6 1l5 5M2.5 5v5h7V5" fill="none" stroke="#fff" stroke-width="1.2"/></svg>Home</li>
  <li><svg width="12" height="12" viewBox="0 0 12 12"><rect x="1.5" y="0.5" width="9" height="11" fill="none" stroke="#777"/><line x1="1.5" y1="4" x2="10.5" y2="4" stroke="#777"/></svg>Appliances</li>
  <li><svg width="12" height="11" viewBox="0 0 12 11"><rect x="0.5" y="0.5" width="11" height="7" fill="none" stroke="#777"/><line x1="3" y1="10" x2="9" y2="10" stroke="#777"/></svg>Computers</li>
  <li><svg width="12" height="11" viewBox="0 0 12 11"><rect x="0.5" y="1.5" width="11" height="7" fill="none" stroke="#777"/><line x1="4" y1="10" x2="8" y2="10" stroke="#777"/></svg>Electronics</li>
  <li><svg width="12" height="12" viewBox="0 0 12 12"><path d="M6 .5 11 2.5V6c0 3-2.5 5-5 5.5C3.5 11 1 9 1 6V2.5Z" fill="none" stroke="#777"/></svg>Home Security</li>
  <li><svg width="12" height="12" viewBox="0 0 12 12"><rect x="3" y="0.5" width="6" height="11" rx="1" fill="none" stroke="#777"/></svg>Mobiles</li>
  <li><svg width="12" height="11" viewBox="0 0 12 11"><path d="M1 6 6 1l5 5M2.5 5v5h7V5" fill="none" stroke="#777"/></svg>Smart Home</li>
  <li><svg width="12" height="12" viewBox="0 0 12 12"><circle cx="6" cy="6" r="3" fill="none" stroke="#777" stroke-width="2" stroke-dasharray="2 1.5"/></svg>Software</li>
</ul>
</nav>

<main class="new-products column abs">
  <h2 class="column-title">New Products</h2>

  <article class="abs" style="left:14px;top:47px;width:356px">
    <div class="photo" role="img" aria-label="Living room with a wall-mounted TV and floor speakers" style="height:167px;background:linear-gradient(180deg,#b35a32,#7a3b22 70%,#3d2a22)">
      <div class="tags"><span class="tag">Home</span><span class="tag">Speakers</span></div>
    </div>
    <h3 class="card-title large">Lorem Ipsum Dolor Sit Amet</h3>
    <div class="byline"><span class="avatar"></span><span class="author">John Smith</span><span>Posted On 12 Aug, 2016</span></div>
  </article>

  <article class="abs" style="left:14px;top:314px;width:172px">
    <div class="photo" role="img" aria-label="Hand touching a smart home wall panel" style="height:145px;background:linear-gradient(135deg,#cfd3d6,#8f969c)">
      <div class="tags"><span class="tag">Home</span></div>
    </div>
    <h3 class="card-title small">Lorem Ipsum dolor sit amet, consectetur elit</h3>
  </article>

  <article class="abs" style="left:198px;top:314px;width:172px">
    <div class="photo" role="img" aria-label="Tablets and phones laid out on a white surface" style="height:145px;background:linear-gradient(135deg,#f1f1f1,#c9a56a 60%,#d9d9d9)">
      <div class="tags"><span class="tag">Home</span></div>
    </div>
    <h3 class="card-title small">Lorem Ipsum dolor sit amet, consectetur elit</h3>
  </article>

  <article class="abs" style="left:14px;top:514px;width:356px">
    <div class="photo" role="img" aria-label="Black smart speaker on a shelf against a brick wall" style="height:167px;background:linear-gradient(90deg,#7c4a35,#3b3836 35%,#2a2a2a 65%,#7c4a35)">
      <div class="tags"><span class="tag">Audio</span></div>
    </div>
    <h3 class="card-title large">Lorem Ipsum Dolor Sit Amet</h3>
    <div class="byline"><span class="avatar"></span><span class="author">John Smith</span><span>Posted On 12 Aug, 2016</span></div>
  </article>
</main>

<aside class="popular column abs">
  <h2 class="column-title">Popular Products</h2>
  <article class="abs" style="left:12px;top:47px;width:151px">
    <div class="photo" role="img" aria-label="Kitchen appliances on a countertop" style="height:120px;background:linear-gradient(135deg,#5a3e2e,#b0927a)"><div class="tags"><span class="tag">Home</span></div></div>
    <h3 class="card-title side">Lorem ipsum dolor sit amet, consectetur</h3>
  </article>
  <article class="abs" style="left:12px;top:230px;width:151px">
    <div class="photo" role="img" aria-label="Smart thermostat on a wall" style="height:120px;background:linear-gradient(135deg,#9aa4ab,#4f5960)"><div class="tags"><span class="tag">Home</span></div></div>
    <h3 class="card-title side">Lorem ipsum dolor sit amet, consectetur</h3>
  </article>
  <article class="abs" style="left:12px;top:413px;width:151px">
    <div class="photo" role="img" aria-label="Laptop with a blue screen on a desk" style="height:120px;background:linear-gradient(135deg,#6b5443,#2b7fc4 55%,#3a3a3a)"><div class="tags"><span class="tag">Home</span></div></div>
    <h3 class="card-title side">Lorem ipsum dolor sit amet, consectetur</h3>
  </article>
  <article class="abs" style="left:12px;top:596px;width:151px">
    <div class="photo" role="img" aria-label="Smart door lock on a wooden door" style="height:120px;background:linear-gradient(135deg,#3a5c86,#a9b3bd)"><div class="tags"><span class="tag">Home</span></div></div>
    <h3 class="card-title side">Lorem ipsum dolor sit amet, consectetur</h3>
  </article>
</aside>

<div class="load-more abs"><svg width="12" height="12" viewBox="0 0 12 12"><path d="M10 6a4 4 0 1 1-1.2-2.9" fill="none" stroke="#fff" stroke-width="1.4"/><path d="M9.5 0.5v3h-3" fill="none" stroke="#fff" stroke-width="1.4"/></svg>Load More</div>

<footer class="site-footer abs">Copyright © 2016 Venlotix.com. All Rights Reserved.</footer>

</body>
</html>
```